Website for a new t-shirt company called bolddawnapperal.com

We are looking for a talented web designer to create a website that aligns with our brand's message and identity centered around the theme of "Bold Dawn." The website should be modern, clean, and visually appealing while also being user-friendly and easy to navigate.

We will be using the Big Commerce platform for our online store section, so the designer should have experience in designing websites on this platform.

We would like the website to have the following elements:

A color scheme that aligns with the brand's identity and message
A homepage that showcases our products and message, with clear calls-to-action for visitors to explore further
A blog section that highlights our brand's philosophy and offers advice and tips for people looking to make positive changes in their lives
An "About Us" section that introduces our brand and team and offers insight into our mission and values
A contact form that allows visitors to easily get in touch with us for inquiries or support
We are open to creative suggestions and ideas from the designer, but we would like the website to have a modern and minimalist aesthetic that resonates with our target audience of 20 to 40-year-olds.

```html
<!DOCTYPE html>
<html lang="en">
<head>
<meta charset="utf-8">
<title>Bold Dawn — T-Shirts</title>
<link href="https://fonts.googleapis.com/css2?family=Poppins:wght@400;500;600;700&family=Mr+Dafoe&display=swap" rel="stylesheet">
<style>
:root{
  --ink:#111111;
  --text:#222222;
  --muted:#555555;
  --bar:#f2f2f2;
  --band:#e9e9e9;
  --foot:#e6e6e6;
  --white:#ffffff;
  --gold:#e9a521;
  --line:#777777;
}
*{box-sizing:border-box;margin:0;padding:0}
html,body{width:1200px;height:3369px;overflow:hidden}
body{font-family:'Poppins',sans-serif;color:var(--text);background:var(--white);position:relative}
.abs{position:absolute}
.script{font-family:'Mr Dafoe',cursive;font-weight:400}

/* top bar */
.topbar{top:0;left:0;width:1200px;height:43px;background:var(--bar)}
.social{left:111px;top:13px;display:flex;gap:8px}
.social span{width:16px;height:16px;background:var(--ink);border-radius:3px}
.promo{right:172px;top:13px;font-size:12px;font-weight:500}
.close{left:1043px;top:13px}

/* header */
.header{top:43px;left:0;width:1200px;height:79px;background:var(--white)}
.phone{left:128px;top:30px;font-size:14px;font-weight:500;display:flex;align-items:center;gap:6px}
.logo{left:0;width:1200px;top:22px;text-align:center;font-size:30px;font-weight:500;letter-spacing:1px}
.tools{left:938px;top:28px;display:flex;gap:12px}

/* nav */
.nav{top:122px;left:0;width:1200px;height:43px;background:var(--bar);font-size:15.5px;font-weight:500}
.nav a{position:absolute;top:10px;color:var(--ink);text-decoration:none}

/* hero */
.hero{top:165px;left:0;width:1200px;height:515px;background:linear-gradient(90deg,#6d6a66 0%,#8d857c 45%,#b6a898 70%,#7f6f61 100%)}
.hero-title{left:171px;top:170px;font-size:62px;color:var(--white);line-height:1}
.hero-copy{left:171px;top:250px;font-size:16px;color:var(--white);line-height:24px;font-weight:500}
.btn-dark{background:var(--ink);color:var(--white);font-weight:600;border-radius:10px;display:flex;align-items:center;justify-content:center}
.hero-btn{left:171px;top:351px;width:134px;height:40px;font-size:15px}
.dots{left:174px;top:427px;display:flex;align-items:center}
.dots i{width:16px;height:16px;border-radius:50%;background:var(--white);display:block}
.dots i.on{border:4px solid var(--white);background:var(--ink)}
.dots b{width:13px;height:2px;background:var(--white);display:block}
.round{width:52px;height:52px;border-radius:50%;background:var(--white);box-shadow:0 2px 8px rgba(0,0,0,.25);display:flex;align-items:center;justify-content:center}

/* section headings */
.heading{left:0;width:1200px;text-align:center}
.heading h2{font-size:64px;line-height:1;color:var(--ink)}
.heading p{font-size:16px;font-weight:500;color:var(--ink);margin-top:6px}
.heading hr{width:102px;border:0;height:3px;background:var(--ink);margin:8px auto 0}

/* product cards */
.card{width:211px}
.photo{width:211px;border-radius:8px}
.card .name{font-size:15px;margin-top:10px;white-space:nowrap}
.card .stars{color:var(--gold);font-size:20px;line-height:22px;letter-spacing:1px;margin-left:2px}
.card .price{font-size:15px;font-weight:600;margin-top:6px;margin-left:2px}

/* about */
.about{top:1286px;left:0;width:1200px;height:427px;background:linear-gradient(100deg,#8a8a8a 0%,#9a9a96 30%,#b39a6e 45%,#c46a3d 60%,#6d9a4e 75%,#b03a63 90%,#4a3a5a 100%)}
.about-title{left:0;width:1200px;text-align:center;top:82px;font-size:62px;color:var(--white)}
.about-copy{left:215px;top:162px;width:780px;font-size:16px;line-height:24.5px;color:var(--white)}
.play{left:569px;top:278px;width:62px;height:62px;border-radius:50%;background:var(--white);display:flex;align-items:center;justify-content:center}

.values{top:1713px;left:0;width:1200px;height:171px;background:var(--band)}
.value h3{font-size:15px;font-weight:600;color:var(--ink)}
.value p{font-size:16px;line-height:24px;margin-top:10px;width:236px;text-align:justify}

/* blog cards */
.post{width:211px}
.post .photo{height:192px;position:relative}
.date{position:absolute;left:0;top:0;background:var(--white);font-size:12px;padding:6px 12px;border-radius:8px 0 8px 0}
.post h4{font-size:15px;font-weight:600;color:var(--ink);margin-top:6px}
.post p{font-size:13px;line-height:21.5px;text-align:justify;margin-top:2px}
.post .more{font-size:15.5px;margin-top:2px;margin-left:2px}

/* contact */
.contact{top:2505px;left:0;width:1200px;height:610px;background:radial-gradient(circle at 20% 75%,#e6e8ea 0,#eef0f1 35%,#f3f4f5 70%)}
.field{border:1px solid #666;background:transparent;font-size:17px;color:#777;padding:5px 14px;font-family:'Poppins',sans-serif}
.submit{left:322px;top:2988px;width:133px;height:40px;font-size:16px;font-weight:700;letter-spacing:.5px}

/* footer */
.footer{top:3115px;left:0;width:1200px;height:209px;background:var(--foot);border-bottom:1px solid var(--line)}
.col h5{font-size:15.5px;font-weight:600;color:var(--ink)}
.col ul{list-style:none;margin-top:14px}
.col li{font-size:13px;line-height:21.5px}
.subscribe{display:flex;margin-top:12px}
.subscribe span{width:161px;height:31px;border:1px solid #555;font-size:12.5px;color:#555;padding:6px 10px}
.subscribe b{width:70px;height:31px;background:var(--ink);color:var(--white);font-size:13px;display:flex;align-items:center;justify-content:center}
.legal{left:113px;top:3337px;font-size:13px}
.cards{left:883px;top:3336px;display:flex;gap:10px}
.cards span{height:16px;background:#333;border-radius:3px}
</style>
</head>
<body>

<!-- top bar -->
<div class="abs topbar">
  <div class="abs social"><span></span><span></span><span></span><span></span><span></span></div>
  <div class="abs promo">50% Off With The Code WELCOME!</div>
  <svg class="abs close" width="17" height="17" viewBox="0 0 17 17"><path d="M2 2L15 15M15 2L2 15" stroke="#111" stroke-width="3"/></svg>
</div>

<!-- header -->
<header class="abs header">
  <div class="abs phone">
    <svg width="18" height="18" viewBox="0 0 24 24"><path d="M5 3h4l2 5-2.5 1.5a11 11 0 0 0 6 6L16 13l5 2v4a2 2 0 0 1-2 2A17 17 0 0 1 3 5a2 2 0 0 1 2-2z" fill="none" stroke="#111" stroke-width="1.6"/></svg>
    +1 555 010 2030
  </div>
  <div class="abs logo">Bold Dawn</div>
  <div class="abs tools">
    <svg width="24" height="24" viewBox="0 0 24 24"><circle cx="10" cy="10" r="7" fill="none" stroke="#111" stroke-width="2"/><path d="M15 15l6 6" stroke="#111" stroke-width="2"/></svg>
    <svg width="24" height="24" viewBox="0 0 24 24"><circle cx="12" cy="8" r="5" fill="none" stroke="#111" stroke-width="2"/><path d="M3 22a9 8 0 0 1 18 0" fill="none" stroke="#111" stroke-width="2"/></svg>
    <svg width="24" height="24" viewBox="0 0 24 24"><path d="M1 3h4l3 12h11l3-9H7" fill="none" stroke="#111" stroke-width="2"/><circle cx="9" cy="20" r="1.8" fill="#111"/><circle cx="18" cy="20" r="1.8" fill="#111"/></svg>
  </div>
</header>

<!-- navigation -->
<nav class="abs nav">
  <a style="left:389px">Home</a>
  <a style="left:470px">About</a>
  <a style="left:551px">Shop All <svg width="10" height="8" viewBox="0 0 10 8"><path d="M1 2l4 4 4-4" fill="none" stroke="#111" stroke-width="1.6"/></svg></a>
  <a style="left:678px">Blog</a>
  <a style="left:746px">Contact</a>
</nav>

<!-- hero -->
<section class="abs hero" role="img" aria-label="Man in sunglasses and a white t-shirt on a city street">
  <h1 class="abs hero-title script">Welcome to Bold Dawn</h1>
  <p class="abs hero-copy">Lorem ipsum dolor sit amet,<br>consectetur adipiscing elit, sed do eiusmod tempor incididunt<br>ut labore et dolore magna aliqua. Quis ipsum suspendisse.</p>
  <div class="abs btn-dark hero-btn">Show Now</div>
  <div class="abs dots"><i class="on"></i><b></b><i></i><b></b><i></i></div>
  <div class="abs round" style="left:85px;top:232px"><svg width="16" height="22" viewBox="0 0 16 22"><path d="M12 2L3 11l9 9" fill="none" stroke="#111" stroke-width="3"/></svg></div>
  <div class="abs round" style="left:1062px;top:232px"><svg width="16" height="22" viewBox="0 0 16 22"><path d="M4 2l9 9-9 9" fill="none" stroke="#111" stroke-width="3"/></svg></div>
</section>

<!-- shop by collection -->
<div class="abs heading" style="top:755px">
  <h2 class="script">Shop By Collection</h2>
  <p>An Exceptionally Experience</p>
  <hr>
</div>

<div class="abs card" style="left:111px;top:895px">
  <div class="photo" style="height:230px;background:linear-gradient(160deg,#3a6fd0,#2a55b8)" role="img" aria-label="Man in a blue sweater cheering"></div>
  <div class="name">Lorem ipsumipsum dolor ...</div>
  <div class="stars">☆☆☆☆☆</div>
  <div class="price">₹ 1,000 -₹ 500.75</div>
</div>
<div class="abs card" style="left:366px;top:895px">
  <div class="photo" style="height:230px;background:linear-gradient(160deg,#d9dfe6,#b9c2cc)" role="img" aria-label="Man in a black t-shirt"></div>
  <div class="name">Lorem ipsumipsum dolor ...</div>
  <div class="stars">☆☆☆☆☆</div>
  <div class="price">₹ 600 - ₹ 300.60</div>
</div>
<div class="abs card" style="left:623px;top:895px">
  <div class="photo" style="height:230px;background:linear-gradient(160deg,#c9c2b8,#9c968e)" role="img" aria-label="Man in a white t-shirt on a street"></div>
  <div class="name">Lorem ipsumipsum dolor ...</div>
  <div class="stars">☆☆☆☆☆</div>
  <div class="price">$1,000 - $800.70</div>
</div>
<div class="abs card" style="left:878px;top:895px">
  <div class="photo" style="height:230px;background:linear-gradient(160deg,#ececec,#d6d3cc)" role="img" aria-label="Man in a white printed t-shirt"></div>
  <div class="name">Lorem ipsumipsum dolor ...</div>
  <div class="stars">☆☆☆☆☆</div>
  <div class="price">$1,500 - $900.50</div>
</div>
<div class="abs round" style="left:67px;top:984px"><svg width="16" height="22" viewBox="0 0 16 22"><path d="M12 2L3 11l9 9" fill="none" stroke="#999" stroke-width="3"/></svg></div>
<div class="abs round" style="left:1080px;top:984px"><svg width="16" height="22" viewBox="0 0 16 22"><path d="M4 2l9 9-9 9" fill="none" stroke="#999" stroke-width="3"/></svg></div>

<!-- about -->
<section class="abs about" role="img" aria-label="Colourful t-shirts hanging on wooden hangers">
  <h2 class="abs about-title script">About Us</h2>
  <p class="abs about-copy">Lorem ipsum dolor sit amet, consectetur adipiscing elit, sed do eiusmod tempor incididunt ut labore et dolore magna aliqua. Quis ipsum suspendisse ultrices gravida. Risus commodo viverra maecenas accumsan lacus vel facilisis.</p>
  <div class="abs play"><svg width="22" height="24" viewBox="0 0 22 24"><path d="M3 1l18 11L3 23z" fill="#111"/></svg></div>
</section>

<section class="abs values">
  <svg class="abs" style="left:190px;top:50px" width="78" height="86" viewBox="0 0 78 86"><path d="M4 43C20 20 58 20 74 43 58 66 20 66 4 43z" fill="none" stroke="#111" stroke-width="3"/><circle cx="39" cy="43" r="12" fill="none" stroke="#111" stroke-width="3"/><circle cx="39" cy="43" r="5" fill="none" stroke="#111" stroke-width="3"/><path d="M39 2v12M39 72v12M10 12l8 8M68 12l-8 8M10 74l8-8M68 74l-8-8" stroke="#111" stroke-width="3"/></svg>
  <div class="abs value" style="left:294px;top:35px"><h3>Vision</h3><p>Lorem ipsum dolor sit amet, consectetur adipiscing elit, sed do dolore magna aliqua.</p></div>
  <svg class="abs" style="left:686px;top:54px" width="70" height="70" viewBox="0 0 70 70"><circle cx="32" cy="38" r="28" fill="none" stroke="#111" stroke-width="3"/><circle cx="32" cy="38" r="18" fill="none" stroke="#111" stroke-width="3"/><circle cx="32" cy="38" r="8" fill="none" stroke="#111" stroke-width="3"/><path d="M32 38L62 8M54 6l8 2 2 8" fill="none" stroke="#111" stroke-width="3"/></svg>
  <div class="abs value" style="left:777px;top:35px"><h3>Mission</h3><p>Lorem ipsum dolor sit amet, consectetur adipiscing elit, sed do dolore magna aliqua.</p></div>
</section>

<!-- recent blogs -->
<div class="abs heading" style="top:1960px">
  <h2 class="script">Recent Blogs</h2>
  <p>An Exceptionally Experience</p>
  <hr>
</div>

<article class="abs post" style="left:111px;top:2096px">
  <div class="photo" style="background:linear-gradient(160deg,#cfcac4,#8e8781)" role="img" aria-label="Man in a black long-sleeve shirt"><span class="date">01st Jul 2023</span></div>
  <h4>Lorem ipsum dolorum ...</h4>
  <p>“Lorem ipsum dolor sit amet, consectetur adipiscing elit, sed do eiusmod tempor incididunt ut labore et dolore magna aliqua.</p>
  <div class="more">Read More</div>
</article>
<article class="abs post" style="left:366px;top:2096px">
  <div class="photo" style="background:linear-gradient(160deg,#b98a62,#d5652b)" role="img" aria-label="Man in an orange printed t-shirt"><span class="date">09th Jul 2023</span></div>
  <h4>Lorem ipsum dolorum ...</h4>
  <p>“Lorem ipsum dolor sit amet, consectetur adipiscing elit, sed do eiusmod tempor incididunt ut labore et dolore magna aliqua.</p>
  <div class="more">Read More</div>
</article>
<article class="abs post" style="left:623px;top:2096px">
  <div class="photo" style="background:linear-gradient(160deg,#9fb27e,#8c8f93)" role="img" aria-label="Man skateboarding in a white t-shirt"><span class="date">31th Jul 2023</span></div>
  <h4>Lorem ipsum dolorum ...</h4>
  <p>“Lorem ipsum dolor sit amet, consectetur adipiscing elit, sed do eiusmod tempor incididunt ut labore et dolore magna aliqua.</p>
  <div class="more">Read More</div>
</article>
<article class="abs post" style="left:878px;top:2096px">
  <div class="photo" style="background:linear-gradient(160deg,#4b4b4b,#2b2b2b)" role="img" aria-label="Man in a black t-shirt by a stone wall"><span class="date">10th Jul 2023</span></div>
  <h4>Lorem ipsum dolorum ...</h4>
  <p>“Lorem ipsum dolor sit amet, consectetur adipiscing elit, sed do eiusmod tempor incididunt ut labore et dolore magna aliqua.</p>
  <div class="more">Read More</div>
</article>

<!-- contact -->
<section class="abs contact"></section>
<div class="abs heading" style="top:2580px">
  <h2 class="script">Contact Us</h2>
  <p>An Exceptionally Experience</p>
  <hr>
</div>
<div class="abs field" style="left:322px;top:2722px;width:253px;height:35px">First name</div>
<div class="abs field" style="left:625px;top:2722px;width:252px;height:35px">Last name</div>
<div class="abs field" style="left:322px;top:2785px;width:253px;height:35px">Email</div>
<div class="abs field" style="left:625px;top:2785px;width:252px;height:35px">Phone Number</div>
<div class="abs field" style="left:322px;top:2848px;width:557px;height:112px;padding-top:12px">Message</div>
<div class="abs btn-dark submit">SUBMIT</div>

<!-- footer -->
<footer class="abs footer">
  <div class="abs col" style="left:111px;top:22px">
    <h5>Contact Us</h5>
    <div style="display:flex;gap:14px;margin-top:14px">
      <svg width="18" height="22" viewBox="0 0 18 22"><path d="M9 1a8 8 0 0 1 8 8c0 6-8 12-8 12S1 15 1 9a8 8 0 0 1 8-8z" fill="#111"/><circle cx="9" cy="9" r="3" fill="#e6e6e6"/></svg>
      <div style="font-size:13px;line-height:16px">consectetur adipiscing elit,<br>tempor incididunt</div>
    </div>
    <div style="display:flex;gap:14px;margin-top:10px;font-size:13px;align-items:center">
      <svg width="18" height="18" viewBox="0 0 24 24"><path d="M5 3h4l2 5-2.5 1.5a11 11 0 0 0 6 6L16 13l5 2v4a2 2 0 0 1-2 2A17 17 0 0 1 3 5a2 2 0 0 1 2-2z" fill="none" stroke="#111" stroke-width="1.6"/></svg>
      +1 555 010 2030
    </div>
  </div>
  <div class="abs col" style="left:416px;top:22px">
    <h5>Navigate</h5>
    <ul><li>About Us</li><li>Theme features</li><li>Shipping &amp; Returns</li><li>Contact Us</li><li>Blog</li><li>Sitemap</li></ul>
  </div>
  <div class="abs col" style="left:639px;top:22px">
    <h5>Categories</h5>
    <ul><li>Shop All</li><li>T-Shirt</li><li>Polo collar t-shirt</li><li>Half sleeve T-shirt</li></ul>
  </div>
  <div class="abs col" style="left:857px;top:22px">
    <h5>Get in Touch!</h5>
    <ul><li>Enter Your Email Address Get Latest</li><li>Offer And Start Shopping</li></ul>
    <div class="subscribe"><span>Your email address</span><b>Click</b></div>
  </div>
</footer>
<div class="abs legal">Powered by StoreCraft © 2023 bold dawn</div>
<div class="abs cards"><span style="width:30px;border-radius:8px"></span><span style="width:34px"></span><span style="width:32px"></span><span style="width:34px"></span><span style="width:32px"></span></div>

</body>
</html>
```